Tolbek cards

I want a simple business card that pops.
Logo on one side.
On side two i want.
"Are you thinking about a new building on your property, or renovating an existing structure? Contact".....
Owners Name: Dale Whitacre
Owners Phone number: 610-555-0187
Address:4076 Copper Ridge RD, Marlow, PA 15530
Committed to Quality, Service, and Integrity

```html
<!DOCTYPE html>
<html lang="en">
<head>
<meta charset="utf-8">
<title>Tolbek Builders LLC – Business Cards</title>
<link href="https://fonts.googleapis.com/css2?family=Arimo:wght@400;700&family=Kalam:wght@400&display=swap" rel="stylesheet">
<style>
  :root {
    --bg: #262626;
    --card: #f3f2f0;
    --brown-dark: #4a3426;
    --brown-mid: #8c765f;
    --brown-light: #a8927a;
    --band-start: #a38c71;
    --band-end: #6a5342;
    --band-text: #f1ece6;
    --rule: #b9ab9b;
  }
  * { box-sizing: border-box; margin: 0; padding: 0; }
  html, body { width: 1200px; height: 576px; overflow: hidden; background: var(--bg); }
  body { position: relative; font-family: "Arimo", Arial, sans-serif; color: var(--brown-dark); }

  .card {
    position: absolute;
    top: 139px;
    width: 482px;
    height: 291px;
    background: var(--card);
    border-radius: 10px;
    overflow: hidden;
  }
  .card--front { left: 102px; }
  .card--back { left: 596px; }

  /* Front */
  .front-brand {
    position: absolute;
    left: 0; right: 0; top: 140px;
    display: flex; flex-direction: column; align-items: center;
    color: var(--brown-dark);
    font-weight: 700;
  }
  .front-brand__row { display: flex; align-items: center; gap: 12px; }
  .front-brand__square { width: 32px; height: 32px; background: var(--brown-dark); }
  .front-brand__name { font-size: 52px; letter-spacing: 1px; line-height: 1; }
  .front-brand__sub { font-size: 17px; letter-spacing: 2.5px; margin-top: 5px; }

  .tagline-band {
    position: absolute; left: 0; right: 0; bottom: 0; height: 29px;
    background: linear-gradient(90deg, var(--band-start), var(--band-end));
    color: var(--band-text);
    font-size: 12.5px;
    display: flex; align-items: center; justify-content: center;
  }

  /* Back */
  .back-brand {
    position: absolute; left: 20px; top: 26px;
    display: flex; align-items: center; gap: 12px;
    color: var(--brown-dark); font-weight: 700;
  }
  .back-brand__square { width: 30px; height: 30px; background: var(--brown-dark); }
  .back-brand__text { display: flex; flex-direction: column; line-height: 1; }
  .back-brand__name { font-size: 32px; letter-spacing: 0.5px; }
  .back-brand__sub { font-size: 10.5px; letter-spacing: 2.6px; margin-top: 2px; }

  .pitch {
    position: absolute; left: 20px; top: 88px; width: 225px;
    font-family: "Kalam", "Comic Sans MS", cursive;
    font-size: 13.5px; line-height: 17.6px;
    color: var(--brown-dark);
  }
  .contact-label {
    position: absolute; left: 20px; top: 152px; width: 204px;
    display: flex; align-items: center; gap: 6px;
    font-size: 9px; color: var(--brown-dark);
  }
  .contact-label::after { content: ""; flex: 1; height: 1px; background: var(--rule); }

  .owner {
    position: absolute; left: 20px; top: 172px;
    font-size: 20px; font-weight: 700; letter-spacing: 0.2px; line-height: 1;
  }
  .owner__first { color: var(--brown-dark); }
  .owner__last { color: var(--brown-light); }

  .details { position: absolute; left: 20px; top: 203px; list-style: none; font-size: 12.5px; line-height: 15.5px; }
  .details li { display: flex; gap: 6px; margin-bottom: 4px; }
  .details svg { flex: none; margin-top: 2px; }

  .back-tagline { position: absolute; left: 20px; top: 263px; font-size: 11px; }

  .decor {
    position: absolute; left: 240px; top: 0; width: 242px; height: 291px;
    background: linear-gradient(135deg, var(--band-start), var(--band-end));
  }
</style>
</head>
<body>
  <section class="card card--front" aria-label="Card front">
    <div class="front-brand">
      <div class="front-brand__row">
        <span class="front-brand__square"></span>
        <span class="front-brand__name">TOLBEK</span>
      </div>
      <span class="front-brand__sub">BUILDERS LLC</span>
    </div>
    <div class="tagline-band">Committed to Quality, Service &amp; Integrity</div>
  </section>

  <section class="card card--back" aria-label="Card back">
    <div class="back-brand">
      <span class="back-brand__square"></span>
      <span class="back-brand__text">
        <span class="back-brand__name">TOLBEK</span>
        <span class="back-brand__sub">BUILDERS LLC</span>
      </span>
    </div>

    <p class="pitch">Are you thinking about a new<br>building on your property, or<br>renovating an existing structure?</p>

    <div class="contact-label">Contact:</div>
    <p class="owner"><span class="owner__first">DALE</span> <span class="owner__last">WHITACRE</span></p>

    <ul class="details">
      <li>
        <svg width="11" height="11" viewBox="0 0 12 12" aria-hidden="true"><circle cx="6" cy="6" r="5.3" fill="none" stroke="#8c765f" stroke-width="1"/><path d="M4 3.2l1 1.2-.6.8c.4.9 1 1.5 1.9 1.9l.8-.6 1.2 1-.7.9C5.6 8.2 3.8 6.4 3.4 4l.6-.8z" fill="#8c765f"/></svg>
        <span>610-555-0187</span>
      </li>
      <li>
        <svg width="11" height="12" viewBox="0 0 12 13" aria-hidden="true"><circle cx="6" cy="6" r="5.3" fill="none" stroke="#8c765f" stroke-width="1"/><path d="M6 2.8a2.3 2.3 0 0 0-2.3 2.3C3.7 6.8 6 9.3 6 9.3s2.3-2.5 2.3-4.2A2.3 2.3 0 0 0 6 2.8zm0 3.2a.9.9 0 1 1 0-1.8.9.9 0 0 1 0 1.8z" fill="#8c765f"/></svg>
        <span>4076 Copper Ridge RD,<br>Marlow, PA 15530</span>
      </li>
    </ul>

    <p class="back-tagline">Committed to Quality, Service &amp; Integrity</p>

    <div class="decor" role="img" aria-label="Large brand symbol decoration in bronze tones"></div>
  </section>
</body>
</html>
```